We need a business card design for a new company located in Cedar Hollow, KS, entitled 'BrightPath Chiropractic & Holistic Center'. Our services include restoration of health and vitality, spinal exam, health assessment, dietary & fitness programs, lymphatic & therapeutic massage, detox & remineralize body wraps, far infrared sauna therapy

Industry/Entity Type

Business

Contact Information for Business Card

BrightPath Chiropractic & Holistic Center, Marlene Okafor LMT, 4215 Elm Ridge Rd., Suite 310, Cedar Hollow, KS 77482, 470-555-0193

```html
<!DOCTYPE html>
<html lang="en">
<head>
<meta charset="utf-8">
<title>BrightPath Chiropractic &amp; Holistic Center – Business Card</title>
<link rel="stylesheet" href="https://fonts.googleapis.com/css2?family=Crimson+Text:wght@400;600&family=Arimo:wght@400&display=swap">
<style>
  :root {
    --page-bg: #e9e6e1;
    --card-bg: #ffffff;
    --ink: #1f1f1f;
    --ink-soft: #3a3a3a;
    --name-blue: #2b86b6;
    --teal: #3cb5a6;
    --faint-blue: #b9c3d6;
    --faint-teal: #cfe3dd;
    --rule: #2a2a2a;
  }
  * { box-sizing: border-box; margin: 0; padding: 0; }
  html, body {
    width: 1200px; height: 892px; overflow: hidden;
    background: var(--page-bg);
  }
  .sheet {
    width: 1200px; height: 892px;
    display: flex; flex-direction: column; align-items: center; justify-content: center;
    gap: 36px;
  }
  .card {
    position: relative;
    width: 700px; height: 400px;
    background: var(--card-bg);
    box-shadow: 0 6px 18px rgba(0,0,0,0.12);
    overflow: hidden;
  }

  /* Front */
  .brand {
    position: absolute; left: 44px; top: 40px;
    display: flex; align-items: center; gap: 18px;
  }
  .brand-dot {
    width: 60px; height: 60px; border-radius: 50%;
    background: var(--teal);
  }
  .brand-name {
    font-family: "Crimson Text", serif;
    font-size: 56px; line-height: 1; color: var(--ink);
    font-weight: 400;
  }
  .brand-tagline {
    position: absolute; left: 124px; top: 104px;
    font-family: "Crimson Text", serif;
    font-size: 24px; line-height: 1.2; color: var(--ink-soft);
  }
  .title-rule {
    position: absolute; left: 190px; top: 200px;
    width: 150px; height: 0; border-top: 1.5px solid var(--rule);
  }
  .side-rule {
    position: absolute; left: 190px; top: 200px;
    width: 0; height: 200px; border-left: 1.5px solid var(--rule);
  }
  .person {
    position: absolute; right: 40px; top: 168px; text-align: right;
  }
  .person-name {
    font-family: "Crimson Text", serif; font-weight: 600;
    font-size: 38px; line-height: 1; color: var(--name-blue);
  }
  .person-role {
    font-family: "Arimo", sans-serif;
    font-size: 20px; line-height: 1; color: var(--ink); margin-top: 6px;
  }
  .contact {
    position: absolute; left: 214px; top: 238px;
    list-style: none;
    font-family: "Arimo", sans-serif; font-size: 19px; color: var(--ink);
  }
  .contact li { display: flex; align-items: flex-start; gap: 12px; line-height: 28px; }
  .contact .icon { flex: none; margin-top: 5px; }
  .contact .indent { padding-left: 30px; }

  /* Back */
  .services-title {
    position: absolute; left: 56px; top: 30px;
    font-family: "Crimson Text", serif; font-weight: 400;
    font-size: 54px; line-height: 1.1; color: var(--ink);
  }
  .services-list {
    position: absolute; left: 60px; top: 108px;
    list-style: none;
    font-family: "Arimo", sans-serif; font-size: 19px; line-height: 34px; color: var(--ink);
    z-index: 1;
  }
  .faint-mark {
    position: absolute; right: 40px; top: 70px;
    display: flex; align-items: center; gap: 18px;
  }
  .faint-dot {
    width: 150px; height: 150px; border-radius: 50%;
    background: var(--faint-teal);
  }
  .faint-name {
    font-family: "Crimson Text", serif; font-size: 50px; color: var(--faint-blue);
    writing-mode: vertical-rl;
  }
</style>
</head>
<body>
<main class="sheet">

  <section class="card card-front" aria-label="Business card front">
    <div class="brand">
      <span class="brand-dot"></span>
      <span class="brand-name">BrightPath</span>
    </div>
    <div class="brand-tagline">Chiropractic &amp; Holistic Center</div>

    <div class="title-rule"></div>
    <div class="side-rule"></div>

    <div class="person">
      <div class="person-name">Daniel Whitcombe</div>
      <div class="person-role">CEO</div>
    </div>

    <ul class="contact">
      <li>
        <svg class="icon" width="18" height="18" viewBox="0 0 18 18" aria-hidden="true"><rect width="18" height="18" rx="2" fill="var(--teal)"/><path d="M5 4.5c0 4.5 3.5 9 8.5 9l.5-2.2-2.3-1-1.2 1.2c-1.5-.8-2.7-2-3.5-3.5l1.2-1.2-1-2.3z" fill="#fff"/></svg>
        <span>470-555-0193</span>
      </li>
      <li>
        <svg class="icon" width="18" height="18" viewBox="0 0 18 18" aria-hidden="true"><rect width="18" height="18" rx="2" fill="var(--teal)"/><rect x="4" y="5.5" width="10" height="7" fill="none" stroke="#fff" stroke-width="1.3"/><path d="M4 5.5l5 4 5-4" fill="none" stroke="#fff" stroke-width="1.3"/></svg>
        <span>care@brightpathhc.com</span>
      </li>
      <li>
        <svg class="icon" width="18" height="18" viewBox="0 0 18 18" aria-hidden="true"><rect width="18" height="18" rx="2" fill="var(--teal)"/><circle cx="9" cy="9" r="5" fill="none" stroke="#fff" stroke-width="1.3"/><path d="M4 9h10M9 4c-2 3-2 7 0 10M9 4c2 3 2 7 0 10" fill="none" stroke="#fff" stroke-width="1"/></svg>
        <span>www.brightpathhc.com</span>
      </li>
      <li>
        <svg class="icon" width="18" height="18" viewBox="0 0 18 18" aria-hidden="true"><rect width="18" height="18" rx="2" fill="var(--teal)"/><path d="M9 14.5s-4-4.2-4-7a4 4 0 0 1 8 0c0 2.8-4 7-4 7z" fill="#fff"/><circle cx="9" cy="7.5" r="1.5" fill="var(--teal)"/></svg>
        <span>Marlene Okafor LMT, 4215 Elm Ridge Rd.,</span>
      </li>
      <li class="indent"><span>Suite 310, Cedar Hollow, KS 77482</span></li>
    </ul>
  </section>

  <section class="card card-back" aria-label="Business card back">
    <h2 class="services-title">Services</h2>
    <ul class="services-list">
      <li>Spinal exam</li>
      <li>Health assessment</li>
      <li>Dietary &amp; fitness programs</li>
      <li>Far infrared sauna therapy</li>
      <li>Restoration of health and vitality</li>
      <li>Detox &amp; remineralize body wraps</li>
      <li>Lymphatic &amp; therapeutic massage</li>
    </ul>
    <div class="faint-mark" aria-hidden="true">
      <span class="faint-dot"></span>
      <span class="faint-name">BrightPath</span>
    </div>
  </section>

</main>
</body>
</html>
```